A New and modern Business Card for Tarwick Trade Solutions Ltd

New and modern Logo and Business Card Attached is the current logo/business card designCurrently the business is called "Tarwick & Co." or TTS Ltd for short. This is subject to change.This business specialises in Telecoms and Energy. We work with the major networks (QV, K7, etc) and also offer Energy Products saving clients money off their energy bills.These are business to business services.The current design incorporates a Pheonix, indicating rebirth, starting something new.We would like to maintain the Phoenix element but a newer modern style.We love colours in the logo 3 max.The aim of this is to be ultra slick and modern. I envisage Tarwick & Co. on one side of the card with long descriptions on the other side.Side 1:TTS Ltd/Logo?Side 2:TTS Ltd/Logo/Graphic?Brogan & Co.Name:Address:Phone:Email:The design is mostly flexible but must incorporate a Phoenix.For example "Tarwick & Co." with a block phoenix behind the text...up to you.

Industry/Entity Type

Telecommunications

Contact Information for Business Card

Tarwick & Co.
Address:
Name:
Phone:
Email:

Logo Text

Tarwick & Co.

Colors
33a6d7
0792cd
acd037
9bcb3c
f78f20
fece3e

Requirements
Must have
• Phoenix
• 3/4 colours max
• Blue representing Technology (wireless)
• Green for Eco Energy
• Orange for Phoenix
• White business card background
Should not have
• phoenix must not all be red/ orange fire, we are a technology service company and the phoenix colours must represent this. Fire is not representative of our company.

```html
<!DOCTYPE html>
<html lang="en">
<head>
<meta charset="utf-8">
<title>Tarwick Trade Solutions – Business Card</title>
<link href="https://fonts.googleapis.com/css2?family=Cinzel:wght@400&family=Lato:wght@400&family=Roboto:wght@500&display=swap" rel="stylesheet">
<style>
  :root {
    --backdrop: #2b2b2b;
    --card-white: #ffffff;
    --tech-blue: #0792cd;
    --wireless-blue: #33a6d7;
    --eco-green: #9bcb3c;
    --eco-green-deep: #86b52c;
    --phoenix-orange: #f78f20;
    --ink: #3d3d3d;
    --rule: #555555;
  }
  html, body {
    margin: 0;
    width: 1200px;
    height: 1200px;
    overflow: hidden;
    background: var(--backdrop);
    font-family: "Lato", sans-serif;
  }
  .canvas { position: relative; width: 1200px; height: 1200px; }

  .card {
    position: absolute;
    top: 310px;
    height: 594px;
    box-sizing: border-box;
    overflow: hidden;
  }
  .card--front { left: 234px; width: 364px; background: var(--card-white); }
  .card--back {
    left: 627px;
    width: 369px;
    background: linear-gradient(165deg, var(--wireless-blue) 0%, var(--tech-blue) 55%, #0a7fb3 80%, var(--eco-green) 100%);
  }

  .brand-mark {
    position: absolute;
    left: 50%;
    top: 110px;
    width: 96px;
    height: 96px;
    margin-left: -48px;
    border-radius: 50%;
    background: var(--phoenix-orange);
  }
  .brand-name {
    position: absolute;
    left: 0;
    right: 0;
    margin: 0;
    text-align: center;
    white-space: nowrap;
    line-height: 1;
  }
  .brand-name__main {
    font-family: "Cinzel", serif;
    font-weight: 400;
    color: var(--tech-blue);
    top: 248px;
    font-size: 46px;
  }
  .brand-name__sub {
    font-family: "Roboto", sans-serif;
    font-weight: 500;
    color: var(--eco-green-deep);
    top: 292px;
    font-size: 14px;
    letter-spacing: 1.2px;
  }

  .contact {
    position: absolute;
    left: 0;
    right: 0;
    top: 390px;
    text-align: center;
    color: var(--ink);
  }
  .contact__name { margin: 0; font-size: 22px; line-height: 24px; color: var(--tech-blue); }
  .contact__role { margin: 0; font-size: 17px; line-height: 20px; }
  .contact__rule { width: 124px; height: 1px; background: var(--rule); margin: 7px auto 6px; }
  .contact__rule--wide { width: 152px; margin-top: 6px; }
  .contact__line { margin: 0; font-size: 17px; line-height: 22px; }

  .card--back .brand-name__main { color: var(--card-white); top: 266px; font-size: 50px; }
  .card--back .brand-name__sub { color: var(--card-white); top: 316px; font-size: 16px; }
</style>
</head>
<body>
<main class="canvas">
  <section class="card card--front" aria-label="Business card front">
    <div class="brand-mark"></div>
    <p class="brand-name brand-name__main">TARWICK</p>
    <p class="brand-name brand-name__sub">TRADE SOLUTIONS LIMITED</p>

    <div class="contact">
      <p class="contact__name">DANIEL HARTLEY</p>
      <p class="contact__role">Managing Director</p>
      <div class="contact__rule"></div>
      <p class="contact__line">044-987 650 321</p>
      <p class="contact__line">hello@tarwickmail.com</p>
      <div class="contact__rule contact__rule--wide"></div>
      <p class="contact__line">87, Harbour Row Lane</p>
      <p class="contact__line">60213,Westmarch</p>
    </div>
  </section>

  <section class="card card--back" role="img" aria-label="Business card back: blue to green brand gradient where a large faint brand graphic belongs">
    <p class="brand-name brand-name__main">TARWICK</p>
    <p class="brand-name brand-name__sub">TRADE SOLUTIONS LIMITED</p>
  </section>
</main>
</body>
</html>
```